Cobalt Ridge Electric Needs A Logo Design

We need a logo for my new company based out of Sacramento, Ca called Cobalt Ridge Electric. The name says it all, my electrical contracting business provides "Cobalt Ridge Professional Work" I'm open to any colors that pop and customers to say Wow. I would love to print my cards on metal.

Industry/Entity Type

Business

Contact Information for Business Card

The card needs to have as follows
Name of company: Cobalt Ridge Electric
My Name: Marco Delvane
Phone # 916-555-0173
CL# 2049381
Email: cobaltridgeelectric@mailnest.example
and a slogan that represent "COBALT RIDGE"

Requirements
Must have
• The card needs to have as follows
• Name of company: Cobalt Ridge Electric
• My Name : Marco Delvane
• Phone # 916-555-0173
• CL# 2049381
• Email: cobaltridgeelectric@mailnest.example
• and a slogan that represent "COBALT RIDGE"
Nice to have
• popping colors
• electrical Arcing

```html
<!DOCTYPE html>
<html lang="en">
<head>
<meta charset="utf-8">
<title>Cobalt Ridge Electric — Business Card</title>
<link rel="stylesheet" href="https://fonts.googleapis.com/css2?family=Open+Sans:wght@400;600;700&display=swap">
<style>
  :root {
    --backdrop: #e6e8ea;
    --card-clear: #f1f3f4;
    --band-front: #14a2d3;
    --band-back: #19addf;
    --brand-blue: #1c9fcf;
    --ink-light: #ffffff;
  }
  * { margin: 0; padding: 0; box-sizing: border-box; }
  html, body {
    width: 1200px;
    height: 900px;
    overflow: hidden;
    background: var(--backdrop);
    font-family: "Open Sans", Arial, sans-serif;
  }
  .canvas { position: relative; width: 1200px; height: 900px; }

  .card {
    position: absolute;
    background: var(--card-clear);
    box-shadow: 0 2px 10px rgba(0,0,0,0.12);
    overflow: hidden;
  }
  .card--front { left: 238px; top: 62px; width: 555px; height: 343px; }
  .card--back  { left: 457px; top: 518px; width: 560px; height: 342px; }

  .card__top { position: absolute; left: 0; top: 0; width: 100%; }
  .card--front .card__top { height: 185px; }
  .card--back .card__top { height: 187px; }

  .brand-name {
    position: absolute;
    left: 0; right: 0;
    top: 78px;
    text-align: center;
    font-size: 28px;
    font-weight: 600;
    letter-spacing: 1px;
    color: var(--brand-blue);
  }

  .card__band {
    position: absolute;
    left: 0; bottom: 0; width: 100%;
  }
  .card--front .card__band { top: 185px; background: var(--band-front); }
  .card--back .card__band { top: 187px; background: var(--band-back); }

  .holder-name {
    position: absolute;
    left: 110px; top: 47px;
    font-size: 17px;
    font-weight: 700;
    color: var(--ink-light);
  }
  .contact-list {
    position: absolute;
    left: 266px; top: 30px;
    list-style: none;
    color: var(--ink-light);
    font-size: 14px;
  }
  .contact-list li {
    display: flex;
    align-items: center;
    height: 20.5px;
  }
  .contact-list svg { width: 11px; height: 11px; margin-right: 9px; fill: var(--ink-light); flex: none; }
  .slogan {
    position: absolute;
    left: 0; right: 0; top: 107px;
    text-align: center;
    font-size: 14.5px;
    color: var(--ink-light);
  }

  .back-name {
    position: absolute;
    left: 0; right: 0; top: 62px;
    text-align: center;
    font-size: 28px;
    font-weight: 600;
    letter-spacing: 1px;
    color: var(--ink-light);
  }
</style>
</head>
<body>
<main class="canvas">
  <section class="card card--front">
    <div class="card__top">
      <p class="brand-name">Cobalt Ridge Electric</p>
    </div>
    <div class="card__band">
      <p class="holder-name">Marco Delvane</p>
      <ul class="contact-list">
        <li>
          <svg viewBox="0 0 24 24" aria-hidden="true"><path d="M6.6 10.8a15.1 15.1 0 0 0 6.6 6.6l2.2-2.2a1 1 0 0 1 1-.25 11.4 11.4 0 0 0 3.6.57 1 1 0 0 1 1 1V20a1 1 0 0 1-1 1A17 17 0 0 1 3 4a1 1 0 0 1 1-1h3.5a1 1 0 0 1 1 1c0 1.25.2 2.45.57 3.57a1 1 0 0 1-.25 1z"/></svg>
          916-555-0173
        </li>
        <li>
          <svg viewBox="0 0 24 24" aria-hidden="true"><path d="M7 1h10a2 2 0 0 1 2 2v18a2 2 0 0 1-2 2H7a2 2 0 0 1-2-2V3a2 2 0 0 1 2-2zm0 3v14h10V4zm5 15.5a1 1 0 1 0 0 2 1 1 0 0 0 0-2z"/></svg>
          2049381
        </li>
        <li>
          <svg viewBox="0 0 24 24" aria-hidden="true"><path d="M2 5h20v14H2zm2 2v.5l8 5 8-5V7l-8 5z"/></svg>
          cobaltridgeelectric@mailnest.example
        </li>
      </ul>
      <p class="slogan">Cobalt Ridge Professional Work</p>
    </div>
  </section>

  <section class="card card--back">
    <div class="card__top"></div>
    <div class="card__band">
      <p class="back-name">Cobalt Ridge Electric</p>
    </div>
  </section>
</main>
</body>
</html>
```